FLYERS REPLIQUE or SIMILAR- PIZZA COMET RECTO / VERSO

Make an identical or similar replica of the flyers as an attachment (front / back) A4 open format, A5 closed format. - The base tomato and cream base pizza products should fall on the same page. I do not have a PDF format - Delete the formula MIDI Menu - Delete the BAR A PATES formula

Target Market(s)

B to C

Colors

Requirements
Must have
• The logo, have similar illustration of qualities
Should not have
• Some things off topic

```html
<!DOCTYPE html>
<html lang="fr">
<head>
<meta charset="utf-8">
<title>Pizza Comet – Flyer recto / verso</title>
<link href="https://fonts.googleapis.com/css2?family=Montserrat:wght@400;500;600;700;800&display=swap" rel="stylesheet">
<style>
:root{
  --backdrop:#bfbfbf;
  --ink:#0e0e0e;
  --panel:#151b24;
  --orange:#f26a21;
  --yellow:#f6c21b;
  --tan:#e9b57a;
  --red:#e8202a;
  --white:#ffffff;
  --soft:#d9d9d9;
}
*{margin:0;padding:0;box-sizing:border-box}
html,body{width:944px;height:1200px;overflow:hidden;background:var(--backdrop)}
body{position:relative;font-family:"Montserrat",Arial,sans-serif;color:var(--white)}
.page{position:absolute;top:311px;width:452px;height:578px;background:linear-gradient(160deg,#1b1b1b,var(--ink) 60%,#161616);overflow:hidden;box-shadow:0 2px 8px rgba(0,0,0,.35)}
.page--front{left:14px}
.page--back{left:478px}
.abs{position:absolute}
.photo{position:absolute}
.center{left:0;right:0;text-align:center}

/* front */
.side-strip{top:0;width:47px;height:460px;background:linear-gradient(180deg,#3a1d12,#1e1411 40%,#2b1a12 70%,#1a1a1a)}
.side-strip--left{left:0}
.side-strip--right{right:0;left:auto;width:48px}
.hero-panel{left:47px;top:0;width:357px;height:460px;background:linear-gradient(180deg,#0f141b,var(--panel) 40%,#1d2733)}
.brand{top:58px;font-weight:700;font-size:12px;letter-spacing:.5px;color:var(--tan)}
.brand-dot{display:inline-block;width:9px;height:9px;border-radius:50%;background:var(--tan);margin-right:6px;vertical-align:0}
.brand-mascot{left:156px;top:14px;width:140px;height:38px;border-radius:20px;background:radial-gradient(circle at 60% 50%,#f0b43c,#c9662a 70%,transparent 71%)}
.title{top:98px;font-weight:800;font-size:28px;color:var(--yellow);letter-spacing:1px}
.title-deco{top:104px;width:26px;height:18px;border-radius:50%;background:radial-gradient(#f7d24a,#c99a20)}
.title-rule{left:141px;top:133px;width:170px;height:5px;background:repeating-linear-gradient(-45deg,#9a9a9a 0 2px,#3a3a3a 2px 4px)}
.phone-hero{top:141px;font-weight:800;font-size:27px;letter-spacing:.5px}
.pizza-photo{left:56px;top:174px;width:333px;height:266px;border-radius:50%/48%;background:radial-gradient(circle at 50% 50%,#d99a55,#b7562c 50%,#6b3a22 68%,rgba(21,27,36,0) 72%)}
.feature{width:90px;text-align:center;top:440px}
.feature svg{display:block;margin:0 auto}
.feature span{display:block;margin-top:4px;font-weight:700;font-size:7px;line-height:8px}
.info-address{font-weight:700;font-size:11px;color:var(--orange)}
.info-line{font-weight:600;font-size:6.6px;line-height:8px}
.info-closed{font-weight:600;font-size:5.5px;color:var(--red)}
.web{font-weight:600;font-size:7px}
.delivery-art{background:linear-gradient(135deg,#d9a23a,#c64a25 60%,#e02a2a)}
.delivery-title{font-weight:700;font-size:8px;color:var(--orange)}
.delivery-sub{font-size:5.5px;color:var(--soft)}

/* back */
.dash-box{border:1px dashed #9a9a9a;border-radius:3px}
.salad-photo{left:27px;top:28px;width:179px;height:109px;background:linear-gradient(135deg,#eef0ea,#6f9a3a 45%,#e06a2e 75%,#f3f3f3)}
.section-title{font-weight:700;color:var(--orange)}
.salad-item{left:218px;font-size:4.6px;color:var(--soft);line-height:6px}
.salad-item b{font-size:8px;color:var(--yellow);font-weight:700;margin-right:3px}
.fries-photo{left:22px;top:154px;width:194px;height:108px;background:linear-gradient(135deg,#8a6a3a,#e9c96a 45%,#f2f2f2 80%)}
.dessert-photo{left:224px;top:154px;width:196px;height:108px;border-radius:4px;background:radial-gradient(circle at 55% 50%,#e6eefc,#6f99e0 55%,#3b6fd3)}
.menu-row{font-weight:600;font-size:11px;line-height:15px}
.drink-row{font-size:9.5px;line-height:12.8px}
.cans-photo{left:193px;top:379px;width:87px;height:70px;background:linear-gradient(90deg,#1f8f3f,#e7731c 35%,#d9141d 60%,#c7c7c7)}
.kids-photo{left:334px;top:364px;width:42px;height:39px;border-radius:50%;background:radial-gradient(#e6963f,#b8492a)}
.kids-title{font-weight:700;font-size:10px;color:var(--yellow)}
.kids-line{font-weight:500;font-size:6.4px;line-height:10.5px}
.phone-small{font-weight:700;font-size:15px;color:var(--red);letter-spacing:.5px}
.social{font-weight:700;font-size:7px}
.social i{display:inline-block;width:9px;height:9px;border-radius:50%;background:#3b5998;margin-right:5px;vertical-align:-1px}
</style>
</head>
<body>

<!-- RECTO -->
<section class="page page--front">
  <div class="abs side-strip side-strip--left" role="img" aria-label="Pizza photo on dark wood, left edge"></div>
  <div class="abs side-strip side-strip--right" role="img" aria-label="Pizza and wooden utensils photo, right edge"></div>
  <div class="abs hero-panel"></div>

  <div class="abs brand-mascot" role="img" aria-label="Mascot illustration holding a pizza slice"></div>
  <div class="abs brand center"><span class="brand-dot"></span>PIZZA COMET</div>

  <div class="abs title-deco" style="left:99px" role="img" aria-label="Small pizza stack illustration"></div>
  <div class="abs title center">PIZZERIA</div>
  <div class="abs title-deco" style="left:327px" role="img" aria-label="Small pizza stack illustration"></div>
  <div class="abs title-rule"></div>
  <div class="abs phone-hero center">03 87 41 20 58</div>

  <div class="photo pizza-photo" role="img" aria-label="Sliced vegetable pizza on slate with rosemary"></div>

  <div class="abs feature" style="left:94px">
    <svg width="34" height="32" viewBox="0 0 34 32"><polygon points="17,1 21,12 33,12 23,19 27,31 17,24 7,31 11,19 1,12 13,12" fill="#f08a4b"/><path d="M12 15h4l2-5 2 1-1 4h4v7h-11z" fill="#fff"/></svg>
    <span>PRODUIT FRAIS</span>
  </div>
  <div class="abs feature" style="left:178px">
    <svg width="34" height="32" viewBox="0 0 34 32"><polygon points="17,1 21,12 33,12 23,19 27,31 17,24 7,31 11,19 1,12 13,12" fill="#f08a4b"/><polygon points="11,12 24,12 17,24" fill="#fff"/></svg>
    <span>LARGE CHOIX</span>
  </div>
  <div class="abs feature" style="left:263px">
    <svg width="34" height="32" viewBox="0 0 34 32"><polygon points="17,1 21,12 33,12 23,19 27,31 17,24 7,31 11,19 1,12 13,12" fill="#f08a4b"/><path d="M12 11l10 11M22 11l-10 11" stroke="#fff" stroke-width="2"/></svg>
    <span>SUR PLACE OU<br>EMPORTER</span>
  </div>

  <svg class="abs" style="left:26px;top:511px" width="70" height="44" viewBox="0 0 70 44"><rect x="9" y="3" width="52" height="32" rx="2" fill="none" stroke="#f26a21" stroke-width="3"/><rect x="1" y="37" width="68" height="5" rx="2" fill="#f26a21"/></svg>
  <div class="abs web" style="left:25px;top:562px">www.pizza-comet.fr</div>

  <div class="abs info-address center" style="top:502px;left:-10px">14 RUE DES LILAS 57100 VALMONT</div>
  <div class="abs info-line center" style="top:517px;left:-10px">LUNDI MERCREDI JEUDI VENDREDI<br>12H00-14H00 / 18H00-22H30</div>
  <div class="abs info-line center" style="top:540px;left:-10px">SAMEDI DIMANCHE JOURS FERIES<br>18H00-22H30</div>
  <div class="abs info-closed center" style="top:560px;left:-10px">Mardi fermé</div>

  <div class="abs delivery-art" style="left:358px;top:503px;width:63px;height:38px;border-radius:4px" role="img" aria-label="Delivery scooter illustration"></div>
  <div class="abs delivery-title" style="left:338px;top:549px">LIVRAISON GRATUITE</div>
  <div class="abs delivery-sub" style="left:348px;top:559px">Lorem Ipsum Dummy Text</div>
</section>

<!-- VERSO -->
<section class="page page--back">
  <div class="abs dash-box" style="left:27px;top:28px;width:394px;height:109px"></div>
  <div class="photo salad-photo" role="img" aria-label="Mixed salad plates with tomatoes and carrots"></div>
  <div class="abs section-title" style="left:222px;top:38px;font-size:19px">SALADES&nbsp;&nbsp;6€00</div>
  <div class="abs salad-item" style="top:63px"><b>NICOISE</b>Lorem Ipsum is simply dummy text of the printing</div>
  <div class="abs salad-item" style="top:76px"><b>CAPRA</b>Lorem Ipsum is simply dummy text of the printing<br>Lorem Ipsum is simply dummy text of the printing</div>
  <div class="abs salad-item" style="top:96px"><b>NORVEGIENNE</b>Lorem Ipsum is simply dummy text<br>Lorem Ipsum is simply dummy text of the printing</div>
  <div class="abs salad-item" style="top:116px"><b>POULET</b>Lorem Ipsum is simply dummy text<br>Lorem Ipsum is simply dummy text</div>

  <div class="photo fries-photo" role="img" aria-label="French fries in a white bowl with sauces"></div>
  <div class="photo dessert-photo" role="img" aria-label="Chocolate-coated ice cream bar on blue"></div>

  <div class="abs section-title" style="left:27px;top:268px;font-size:16px">SNACKING</div>
  <div class="abs menu-row" style="left:27px;top:295px">Frites<br>Nuggets 8 pcs</div>
  <div class="abs menu-row" style="left:139px;top:295px">2€00<br>4€00</div>

  <div class="abs section-title" style="left:240px;top:268px;font-size:16px;color:var(--yellow)">DESSERTS</div>
  <div class="abs menu-row" style="left:240px;top:295px">Tiramisu<br>Glacier Dolce<br>Bâton Choco</div>
  <div class="abs menu-row" style="left:353px;top:295px">2€50<br>3€00<br>2€50</div>

  <div class="abs dash-box" style="left:27px;top:353px;width:394px;height:110px"></div>
  <div class="abs section-title" style="left:45px;top:366px;font-size:15px;color:var(--yellow)">BIOSSONS</div>
  <div class="abs drink-row" style="left:45px;top:389px">Canette<br>Eauo,51<br>Volt Energy<br>Bouteille o,51<br>Bouteille1,51</div>
  <div class="abs drink-row" style="left:127px;top:389px">1€50<br>1€00<br>2€00<br>2€00<br>3€00</div>
  <div class="photo cans-photo" role="img" aria-label="Assorted soda cans"></div>
  <div class="photo kids-photo" role="img" aria-label="Small whole pizza"></div>
  <div class="abs kids-title" style="left:315px;top:407px">MENU ENFANT</div>
  <div class="abs kids-line" style="left:288px;top:420px;width:128px;text-align:center">PETITE PIZZA MARGARITA<br>POMPOTES, JUS SOLEIL &amp;<br>UNE SURPRISE <b style="color:var(--yellow)">6€00</b></div>

  <svg class="abs" style="left:27px;top:494px" width="67" height="40" viewBox="0 0 70 44"><rect x="9" y="3" width="52" height="32" rx="2" fill="none" stroke="#f26a21" stroke-width="3"/><rect x="1" y="37" width="68" height="5" rx="2" fill="#f26a21"/></svg>
  <div class="abs web" style="left:25px;top:542px">www.pizza-comet.fr</div>

  <div class="abs info-address center" style="top:486px;left:-4px">14 RUE DES LILAS 57100 VALMONT</div>
  <div class="abs info-line center" style="top:500px;left:-4px">LUNDI MERCREDI JEUDI VENDREDI<br>12H00-14H00 / 18H00-22H30</div>
  <div class="abs info-line center" style="top:522px;left:-4px">SAMEDI DIMANCHE JOURS FERIES<br>18H00-22H30</div>
  <div class="abs info-closed center" style="top:540px;left:-4px">Mardi fermé</div>
  <div class="abs phone-small center" style="top:549px;left:-4px">03 87 41 20 58</div>

  <div class="abs delivery-art" style="left:346px;top:485px;width:57px;height:39px;border-radius:4px" role="img" aria-label="Delivery scooter illustration"></div>
  <div class="abs delivery-title" style="left:325px;top:528px">LIVRAISON GRATUITE</div>
  <div class="abs delivery-sub" style="left:334px;top:538px">Lorem Ipsum Dummy Text</div>
  <div class="abs social" style="left:308px;top:555px"><i></i>PIZZA COMET VALMONT</div>
</section>

</body>
</html>
```